Willow Cradle Pregnancy and Baby Massage

I need a web design for a new business, WILLOW CRADLE PREGNANCY AND BABY MASSAGE that I am in the process of setting up in the suburbs of Perth, Western Australia. The business is owned and operated by myself and my intention is to service Pregnant Mothers and Parents of Young Babies that would benefit from massage. I would like to have a "Home Page" and pages for "About Me", "Pregnancy Massage", "Baby Massage", a Pricing Page for Pregnancy Massage Sessions, a Pricing Page for Baby Massage Sessions, and a "Contact Me" page to allow clients to either contact me with queries or book available pregnancy massage sessions on a particular day of the week. I would also like a "News" page that would include articles I have written, news about new courses and a link to my Facebook page (yet to be set up). I would like to keep the colour schemes similar to my logo design colours. I need the design to be easy to follow and to appeal to a younger audience (20's to mid 30's).
The target audience is pregnant mothers-to-be wishing to receive massage treatments, and new parents and grandparents of small babies that would like to learn how to massage their babies.
The look and feel should be modern, professional, elegant and feminine.
I need the design to be in a standard format such that I can update the content by myself ( and does not need specialised software) as the company and business progresses.

Target Market(s)

Contact Information for Business Card

Card should have rounded edges. Design should have the same "feel" as the website. Contact Details of my business address, mobile phone, email and website should be included.

Font styles to use
Script

Requirements
Must have
• Same colours as logo design. In cmyk system, the colours are: 20,60,0,0 which best result is pantone 681 and 40,40,0,0 which best result is pantone 2645. Card should include the logo design.

```html
<!DOCTYPE html>
<html lang="en">
<head>
<meta charset="utf-8">
<title>Willow Cradle Pregnancy and Baby Massage – Pregnancy Massage Sessions</title>
<link href="https://fonts.googleapis.com/css2?family=Amaranth&family=Indie+Flower&display=swap" rel="stylesheet">
<style>
  :root {
    --teal: #9cc5c0;
    --page: #ece0e0;
    --band: #e5d0d1;
    --panel: #e9d9d9;
    --pill: #a9c4c0;
    --pink: #d652a9;
    --violet: #b48ad0;
    --ink: #1f1a1c;
    --dur-label: #d7a0b1;
    --dur-value: #dcafcd;
    --cost-label: #c6a7c0;
    --cost-value: #c1b0d6;
  }
  * { box-sizing: border-box; margin: 0; padding: 0; }
  html, body { width: 873px; height: 1200px; overflow: hidden; }
  body { background: var(--page); font-family: "Amaranth", sans-serif; color: var(--ink); position: relative; }

  .site-header { position: absolute; top: 0; left: 0; width: 873px; height: 113px; background: var(--teal); }
  .menu-button { position: absolute; left: 22px; top: 28px; }
  .search-button { position: absolute; right: 22px; top: 24px; }
  .brand { position: absolute; left: 0; right: 0; top: 14px; text-align: center; color: var(--pink); font-family: "Indie Flower", cursive; line-height: 1; }
  .brand-name { display: block; font-size: 40px; }
  .brand-tag { display: block; font-size: 17px; margin-top: 4px; }

  .breadcrumb { position: absolute; left: 38px; top: 128px; height: 36px; padding: 0 18px; background: var(--pill); border-radius: 8px; font-size: 17px; line-height: 36px; color: var(--pink); }

  .page-title { position: absolute; left: 0; top: 196px; width: 873px; height: 86px; background: var(--band); text-align: center; font-family: "Indie Flower", cursive; font-weight: 400; font-size: 44px; line-height: 86px; color: var(--violet); }

  .section-title { position: absolute; left: 0; top: 307px; width: 873px; height: 78px; background: var(--band); padding-left: 62px; font-family: "Indie Flower", cursive; font-weight: 400; font-size: 30px; line-height: 78px; color: var(--pink); }

  .session-info { position: absolute; left: 0; top: 397px; width: 873px; height: 440px; background: var(--panel); padding: 20px 40px 0; text-align: center; font-size: 27px; line-height: 34px; }
  .session-info p { width: 800px; margin: 0 auto; }

  .session-details { position: absolute; left: 0; top: 873px; width: 873px; border-collapse: collapse; font-size: 29px; }
  .session-details th { width: 214px; text-align: right; font-weight: 400; padding-right: 22px; }
  .session-details td { padding-left: 30px; text-align: left; }
  .row-duration { height: 102px; }
  .row-duration th { background: var(--dur-label); }
  .row-duration td { background: var(--dur-value); }
  .row-cost { height: 126px; }
  .row-cost th { background: var(--cost-label); }
  .row-cost td { background: var(--cost-value); }

  .site-footer { position: absolute; left: 0; top: 1101px; width: 873px; height: 99px; background: var(--teal); display: flex; justify-content: space-between; align-items: center; padding: 0 78px; }
  .social-link { width: 44px; height: 44px; border-radius: 50%; background: var(--pink); display: block; }
</style>
</head>
<body>
  <header class="site-header">
    <svg class="menu-button" width="56" height="48" viewBox="0 0 56 48" aria-label="Menu">
      <rect x="0" y="0" width="56" height="10" rx="5" fill="#d652a9"/>
      <rect x="0" y="19" width="56" height="10" rx="5" fill="#d652a9"/>
      <rect x="0" y="38" width="56" height="10" rx="5" fill="#d652a9"/>
    </svg>
    <div class="brand">
      <span class="brand-name">Willow Cradle</span>
      <span class="brand-tag">Pregnancy and Baby Massage</span>
    </div>
    <svg class="search-button" width="62" height="62" viewBox="0 0 62 62" aria-label="Search">
      <circle cx="25" cy="25" r="19" fill="none" stroke="#d652a9" stroke-width="7"/>
      <line x1="39" y1="39" x2="57" y2="57" stroke="#d652a9" stroke-width="10" stroke-linecap="round"/>
    </svg>
  </header>

  <nav class="breadcrumb">Home &lt; Pregnancy Massage Sessions</nav>

  <h1 class="page-title">Pregnancy Massage Sessions Available</h1>

  <h2 class="section-title">Pregnancy Massage Session</h2>

  <section class="session-info">
    <p>Each session begins with a consultation to assess any high-risk factors, and to review any changes the body has undergone since the last session. This way the massage can be given in a safe manner.</p>
    <p>The side-lying position is used with pillows for support. This is a comfortable resting position, and minimises pressure on one of the major blood vessels. This reduces the risk of Supine Hypotensive Syndrome, which can cause dizziness and fainting. Also with this position, there is no pressure on the lower back.</p>
  </section>

  <table class="session-details">
    <tr class="row-duration"><th>Duration:</th><td>75 mins session</td></tr>
    <tr class="row-cost"><th>Cost:</th><td>$115 - including 15 mins consultation.</td></tr>
  </table>

  <footer class="site-footer">
    <span class="social-link" role="img" aria-label="Social network link"></span>
    <span class="social-link" role="img" aria-label="Social network link"></span>
    <span class="social-link" role="img" aria-label="Social network link"></span>
    <span class="social-link" role="img" aria-label="Social network link"></span>
    <span class="social-link" role="img" aria-label="Social network link"></span>
  </footer>
</body>
</html>
```